Homemaking training schools needs a Business Card design

Designer, Hello!

No special requirements, good-looking enough.
--------------------------------------------------------------------------

Name: Marcus Dole
Chairman
Tel: 0574-71948263
Mobile: 13857420916
Email: kelvora@mailnest.example
Web: www.prt2019.example
Add: No.258, LanpingJie, BeiyuanQu, Ningbo, Zhejiang

LOGO
Ningbo PRT Homemaking Training School

Target Market(s)

pregnant women, mothers, infants, the elderly and families, including cleaning, cooking, nursing training.

Industry/Entity Type

Business

Contact Information for Business Card

Name: Marcus Dole
Chairman
Tel: 0574-71948263
Mobile: 13857420916
Email: kelvora@mailnest.example
Web: www.prt2019.example

LOGO

Font styles to use
Serif
Sans Serif
Decorative

Requirements
Nice to have
• Feels: clean, specifications, safety, comfort, warmth and happiness.

```html
<!DOCTYPE html>
<html lang="en">
<head>
<meta charset="utf-8">
<title>PRT Homemaking Business Cards</title>
<link rel="stylesheet" href="https://fonts.googleapis.com/css2?family=Arimo:wght@400;700&display=swap">
<style>
  :root {
    --bg: #e7ddd0;
    --card: #fbfbf9;
    --blue: #1f6ea8;
    --magenta: #e0197d;
    --ink: #4a4a4a;
    --rule: #6b6b6b;
  }
  * { margin: 0; padding: 0; box-sizing: border-box; }
  html, body { width: 1200px; height: 794px; overflow: hidden; }
  body {
    background: var(--bg);
    position: relative;
    font-family: "Arimo", Arial, sans-serif;
  }
  .card {
    position: absolute;
    width: 540px;
    height: 320px;
    background: var(--card);
    box-shadow: 0 6px 18px rgba(80, 60, 40, 0.18);
  }
  .card--front { left: 150px; top: 70px; }
  .card--back { left: 510px; top: 410px; }

  /* Front */
  .brand {
    position: absolute;
    left: 0; right: 0; top: 126px;
    display: flex;
    flex-direction: column;
    align-items: center;
  }
  .brand__row {
    display: flex;
    align-items: center;
    gap: 12px;
  }
  .brand__square {
    width: 16px; height: 16px;
    background: var(--magenta);
  }
  .brand__name {
    font-family: "Arimo", Arial, sans-serif;
    font-weight: 700;
    font-size: 38px;
    line-height: 1;
    color: var(--blue);
  }
  .brand__tagline {
    margin-top: 10px;
    font-size: 15px;
    color: var(--ink);
    letter-spacing: 0.5px;
  }

  /* Back */
  .rule {
    position: absolute;
    left: 90px; right: 90px;
    height: 1px;
    background: var(--rule);
  }
  .rule--top { top: 84px; }
  .rule--mid { top: 162px; }
  .rule--bottom { top: 262px; }
  .person {
    position: absolute;
    left: 0; right: 0; top: 100px;
    text-align: center;
  }
  .person__name {
    font-weight: 700;
    font-size: 22px;
    color: var(--blue);
  }
  .person__title {
    font-size: 15px;
    color: var(--magenta);
    margin-top: 3px;
  }
  .contact {
    position: absolute;
    left: 0; right: 0; top: 174px;
    text-align: center;
    font-size: 14px;
    line-height: 25px;
    color: var(--ink);
  }
  .contact__label { color: var(--blue); font-weight: 700; }
  .contact__web { font-weight: 700; color: var(--blue); }
  .contact__web span { color: var(--magenta); }
</style>
</head>
<body>
  <section class="card card--front" aria-label="Card front">
    <div class="brand">
      <div class="brand__row">
        <span class="brand__square"></span>
        <div class="brand__name">PRT Homemaking</div>
      </div>
      <div class="brand__tagline">Training &amp; Services</div>
    </div>
  </section>

  <section class="card card--back" aria-label="Card back">
    <div class="rule rule--top"></div>
    <div class="person">
      <div class="person__name">Marcus Dole</div>
      <div class="person__title">Chairman</div>
    </div>
    <div class="rule rule--mid"></div>
    <div class="contact">
      <div>No.258, LanpingJie, BeiyuanQu, Ningbo, Zhejiang</div>
      <div>
        <span class="contact__label">P:</span> 0574-71948263
        <span class="contact__label">M:</span> 13857420916
        <span class="contact__label">E:</span> kelvora@mailnest.example
      </div>
      <div class="contact__web">www.<span>prt2019</span>.example</div>
    </div>
    <div class="rule rule--bottom"></div>
  </section>
</body>
</html>
```